whitening syringe artwork design

3ml syringe with silkscreen printing:
sample:
https://www.quorvashop.example/Velvo-Crane-Whitening-Syringes-Carbamide/dp/Q51842KX93/ref=sr_1_6?crid=7ZP42WQ81LMRT&dchild=1&keywords=whitening+syringes&qid=1698802214&sprefix=whitening+sy%2Caps%2C150&sr=8-6
inside the writing:
"teeth whitening gel " change to "Orvanne WHITENING GEL"
"Advanced formula" change to our logo and "Not all gels are created equal. "

additional requirements:
Inches: 2.01" wide x 1.34" around

CM: 5.1cm wide x 3.4cm around

See attached template: Generic_Syringe Labels 3ml_Silkscreen.pdf

- Leave the volume gage where it is, so it prints correctly on the syringe

- Feel free to change the color and font style

- An "identifying marker" is required: Teeth Whitening Syringe or Teeth Whitening Gel (for example)

- Replace "Teeth Whitening Gel - Advanced Formula" with your text and logo - it is there as a placeholder

-We require PDF files created to print ready specifications. Color images should be down-sampled to 300DPI

-Please provide us your Tintora color references for the color used in your artwork

https://www.tintora.example/color-finder#/pick?tintoraBook=tintoraSolidCoatedV3M2

-Please ensure that all fonts are embedded in the PDF document or make sure you convert fonts to outlines to prevent any issues with fonts (AI-Type-Create Outlines)

We will need your print ready artwork in a high resolution PDF file

teeth whitening ecommerce

• follow the guide document, and add text I want, color code from Tintora is provided

```html
<!DOCTYPE html>
<html lang="en">
<head>
<meta charset="utf-8">
<title>Mireo Whitening Pen – Syringe Silkscreen Artwork</title>
<link rel="stylesheet" href="https://fonts.googleapis.com/css2?family=Yellowtail&family=Montserrat:wght@600&family=Barlow+Condensed:wght@700&display=swap">
<style>
  :root {
    --paper: #ffffff;
    --ink-top: #1e6fb5;
    --ink-bottom: #2b2a6c;
    --brand-navy: #2e2a6e;
    --gauge-ink: #25407f;
  }
  html, body {
    margin: 0;
    padding: 0;
    width: 1200px;
    height: 718px;
    overflow: hidden;
    background: var(--paper);
  }
  .artboard {
    display: block;
    width: 1200px;
    height: 718px;
  }
  .product-title {
    font-family: "Yellowtail", cursive;
    font-size: 66px;
  }
  .product-title--gel { font-size: 60px; }
  .brand-name {
    font-family: "Montserrat", sans-serif;
    font-weight: 600;
    fill: var(--brand-navy);
    letter-spacing: 3px;
  }
  .brand-dot { fill: var(--brand-navy); }
  .gauge-line {
    stroke: var(--gauge-ink);
    stroke-width: 3;
  }
  .gauge-label {
    font-family: "Barlow Condensed", sans-serif;
    font-weight: 700;
    font-size: 24px;
    fill: var(--gauge-ink);
  }
  .gauge-unit {
    font-family: "Montserrat", sans-serif;
    font-weight: 600;
    font-size: 17px;
    fill: var(--gauge-ink);
  }
</style>
</head>
<body>
<svg class="artboard" viewBox="0 0 1200 718" xmlns="http://www.w3.org/2000/svg">
  <defs>
    <linearGradient id="ink-gradient" x1="0" y1="0" x2="0" y2="1">
      <stop offset="0" stop-color="var(--ink-top)"/>
      <stop offset="1" stop-color="var(--ink-bottom)"/>
    </linearGradient>
  </defs>

  <!-- Pen label, upper -->
  <g class="label label--pen-upper">
    <text class="product-title" x="104" y="240" textLength="448" lengthAdjust="spacingAndGlyphs" fill="url(#ink-gradient)">Mireo Whitening Pen</text>
    <text class="brand-name" x="312" y="277" font-size="22" text-anchor="middle">KELVORA</text>
    <circle class="brand-dot" cx="312" cy="298" r="9"/>
  </g>

  <!-- Pen label, lower -->
  <g class="label label--pen-lower">
    <text class="product-title" x="94" y="479" textLength="448" lengthAdjust="spacingAndGlyphs" fill="url(#ink-gradient)">Mireo Whitening Pen</text>
    <text class="brand-name" x="324" y="516" font-size="22" text-anchor="middle">KELVORA</text>
    <circle class="brand-dot" cx="324" cy="536" r="9"/>
  </g>

  <!-- Gel syringe label -->
  <g class="label label--gel">
    <text class="product-title product-title--gel" x="709" y="263" textLength="363" lengthAdjust="spacingAndGlyphs" fill="url(#ink-gradient)">Teeth Whitening Gel</text>
    <text class="brand-name" x="900" y="286" font-size="17" text-anchor="middle" letter-spacing="2">KELVORA</text>
    <circle class="brand-dot" cx="900" cy="301" r="7"/>
  </g>

  <!-- Volume gauge -->
  <g class="volume-gauge">
    <line class="gauge-line" x1="661" y1="375" x2="661" y2="438"/>
    <line class="gauge-line" x1="730" y1="399" x2="730" y2="438"/>
    <line class="gauge-line" x1="800" y1="375" x2="800" y2="438"/>
    <line class="gauge-line" x1="879" y1="399" x2="879" y2="438"/>
    <line class="gauge-line" x1="957" y1="375" x2="957" y2="438"/>
    <line class="gauge-line" x1="1026" y1="399" x2="1026" y2="438"/>
    <line class="gauge-line" x1="1096" y1="375" x2="1096" y2="438"/>

    <text class="gauge-label" transform="translate(738 378) rotate(-90)">½</text>
    <text class="gauge-label" transform="translate(808 365) rotate(-90)">1</text>
    <text class="gauge-label" transform="translate(887 388) rotate(-90)">1½</text>
    <text class="gauge-label" transform="translate(965 367) rotate(-90)">2</text>
    <text class="gauge-label" transform="translate(1034 390) rotate(-90)">2½</text>
    <text class="gauge-label" transform="translate(1104 367) rotate(-90)">3</text>
    <text class="gauge-unit" transform="translate(1118 432) rotate(-90)">ml/cc</text>
  </g>
</svg>
</body>
</html>
```